Redesign Merle's RV Park & Lodge Website, Leeds, North Dakota

I need a totally re-designed website for my RV Park / Lodge. I want to not only provide information on my RV Park / Lodge, I want to provide my customers with information on the town and area attractions. I want to provide rate information. Ideally, I would like to have a button/page for each section: Welcome & Information, Area Attractions, Welcome to Leeds, Rates, Who's Merle?!, FAQ's and Where are we?. I don't know if this would be more expensive the more pages you have? If more pages is too expensive, then we can combine info on less pages. I want my logo included on the web page. I want Studio Flock to take down my old website and use the same address to put up my newly designed website.

Target Market(s)

Full time RVers, People who camp, hunt fish, People who recreate on Devils Lake, People who are looking for meeting/conference space, people who are looking for party venue

Industry/Entity Type

Accommodation

Number of Pages Required

3 page

Requirements
Must have
• I want a cozy, welcoming type web site. No super dark colors. Bright and cheerful.
• Must be simple and organized.
• NOTE: I have a file of pictures of the interior of Merle's Lodge that must be included in website. Please request this file if you will be designing my project as the files are too large to upload through Studio Flock.
Nice to have
• If you cannot open any of the files listed, please notify me.
Should not have
• No stark or super-formal designs.

```html
<!DOCTYPE html>
<html lang="en">
<head>
<meta charset="utf-8">
<title>Merle's RV Park &amp; Lodge – Leeds ND</title>
<link href="https://fonts.googleapis.com/css2?family=Special+Elite&family=Open+Sans:wght@400;600;700&family=Montserrat:wght@600;700&display=swap" rel="stylesheet">
<style>
:root{
  --red:#b2121e;
  --red-dark:#8e0d17;
  --blue:#2f4d9a;
  --grey-bg:#f1f1f1;
  --ink:#2a2a2a;
  --text:#4a4a4a;
  --line:#d9d9d9;
  --footer:#2d2d2d;
  --footer-deep:#222;
  --white:#fff;
}
*{box-sizing:border-box;margin:0;padding:0}
html,body{width:1200px;height:4215px;overflow:hidden}
body{font-family:"Open Sans",Arial,sans-serif;color:var(--text);background:var(--white);position:relative;font-size:13px;line-height:1.65}
.abs{position:absolute}
h2.title{font-family:"Special Elite","Courier New",monospace;font-weight:400;color:var(--ink);font-size:22px;line-height:1.3}
ul.bullets{list-style:none}
ul.bullets li{position:relative;padding-left:20px;margin-bottom:9px;font-size:12.5px}
ul.bullets li::before{content:"";position:absolute;left:2px;top:6px;width:6px;height:6px;background:var(--red);transform:rotate(45deg)}
.photo{box-shadow:0 4px 10px rgba(0,0,0,.25)}

/* header / hero */
.hero{left:0;top:0;width:1200px;height:620px;overflow:hidden}
.hero-photo{position:absolute;inset:0;background:linear-gradient(180deg,#c9dcea 0%,#e4edf3 30%,#8b9aa5 45%,#a33a3e 52%,#9ba4a8 62%,#7a9a50 75%,#5f7f3a 100%)}
.brand{left:40px;top:20px;display:flex;align-items:center;gap:10px;font-family:"Special Elite","Courier New",monospace;font-size:22px;color:var(--ink);width:220px;line-height:1.2}
.brand .mark{width:34px;height:34px;background:var(--red);flex:none}
.nav{left:335px;top:55px;display:flex;gap:28px;font-size:12.5px;color:var(--ink)}
.nav a{color:inherit;text-decoration:none}
.nav a.active{color:var(--red);font-weight:700;border-bottom:2px solid var(--red);padding-bottom:4px}
.call{right:60px;top:16px;font-size:12px;color:var(--ink);display:flex;align-items:center;gap:8px}
.call strong{color:var(--red);font-size:19px;font-weight:700}
.hero-headline{left:0;width:1200px;top:418px;text-align:center;font-family:"Montserrat",Arial,sans-serif;font-weight:700;color:var(--white);font-size:32px;line-height:1.25;text-shadow:0 2px 6px rgba(0,0,0,.5)}
.dots{left:570px;top:518px;display:flex;gap:12px}
.dots span{width:9px;height:9px;border-radius:50%;background:rgba(255,255,255,.7)}
.dots span.on{background:var(--red)}

/* welcome */
.welcome-text{left:200px;top:735px;width:380px}
.welcome-text p{margin-top:26px;font-size:12.5px}
.divider{left:642px;top:720px;width:1px;height:200px;background:var(--line)}
.portrait{left:715px;top:660px;width:275px;height:275px;border-radius:50%;background:radial-gradient(circle at 50% 40%,#c6a792,#8f7566 60%,#cfcfcf);border:6px solid #eee}

/* grey sections */
.band-grey{background:var(--grey-bg);left:0;width:1200px}
.copy{width:450px}
.copy p{margin-top:18px;font-size:12.5px}
.copy ul{margin-top:18px}
.btn-red{display:inline-block;background:var(--red);color:var(--white);font-weight:700;font-size:12px;padding:8px 22px;text-transform:uppercase}

/* rates */
.rates-title{left:0;width:1200px;top:3085px;text-align:center;font-size:24px}
.card{top:3155px;width:310px;height:350px;background:var(--white);border:1px solid var(--line);text-align:center}
.card h3{background:var(--red);color:var(--white);font-size:16px;font-weight:700;height:56px;line-height:56px}
.card .body{padding:18px 26px;font-size:12.5px;line-height:1.55}
.card hr{border:none;border-top:1px solid var(--line);margin:14px 0}
.price{color:var(--red);font-weight:700;font-size:28px;line-height:1.1}
.price small{display:block;color:var(--text);font-size:11px;font-weight:400}
.prices{display:flex;justify-content:center;gap:20px}
.label{font-weight:700;font-size:11px;color:var(--ink)}

/* reviews band */
.reviews{left:0;top:3570px;width:1200px;height:265px;background:var(--blue);text-align:center;color:var(--white)}
.reviews p{margin-top:50px;font-family:"Montserrat",Arial,sans-serif;font-size:22px;font-weight:600;line-height:1.35}
.fb-btn{display:inline-flex;align-items:center;margin-top:28px;background:var(--white);color:var(--blue);font-weight:700;font-size:13px;height:46px}
.fb-btn .sq{width:46px;height:46px;border-right:1px solid var(--line);display:flex;align-items:center;justify-content:center}
.fb-btn .sq i{width:14px;height:14px;background:var(--blue);display:block}
.fb-btn span.t{padding:0 20px;letter-spacing:.5px}

/* footer */
.footer{left:0;top:3835px;width:1200px;height:320px;background:var(--footer);color:#ddd}
.footer h4{font-size:12px;font-weight:700;color:var(--white);letter-spacing:.5px}
.foot-brand{left:130px;top:70px;font-family:"Special Elite","Courier New",monospace;font-size:26px;color:var(--white);width:200px;line-height:1.25;display:flex;gap:12px;align-items:flex-start}
.foot-brand .mark{width:36px;height:36px;background:var(--white);flex:none;margin-top:4px}
.follow{left:345px;top:95px}
.follow ul{list-style:none;margin-top:20px}
.follow li{display:flex;align-items:center;gap:10px;margin-bottom:14px;font-size:12px}
.follow li i{width:24px;height:24px;border-radius:50%;background:var(--blue);display:block}
.contact{left:520px;top:95px}
.contact ul{list-style:none;margin-top:20px}
.contact li{display:flex;gap:10px;margin-bottom:16px;font-size:12px;line-height:1.4}
.map{left:750px;top:70px;width:315px;height:200px;background:linear-gradient(135deg,#e9e6df,#d9e4d2 50%,#e7e1c8);border:4px solid var(--white)}
.copyright{left:0;top:4155px;width:1200px;height:60px;background:var(--footer-deep);color:#aaa;text-align:center;line-height:60px;font-size:11px}
</style>
</head>
<body>

<!-- Hero -->
<section class="abs hero">
  <div class="hero-photo" role="img" aria-label="Photo of the red-roofed lodge building on the prairie under a blue sky"></div>
  <svg class="abs" style="left:0;top:520px" width="1200" height="100" viewBox="0 0 1200 100" preserveAspectRatio="none">
    <path d="M0 45 Q600 120 1200 30 L1200 100 L0 100 Z" fill="#fff"/>
    <path d="M0 45 Q600 120 1200 30 L1200 48 Q600 130 0 60 Z" fill="#b2121e"/>
  </svg>
</section>
<svg class="abs" style="left:0;top:0" width="1200" height="110"><rect width="1200" height="110" fill="#fff" opacity=".9"/></svg>
<div class="abs brand"><span class="mark"></span>Merle's RV Park &amp; Lodge Leeds ND</div>
<div class="abs call">
  <svg width="14" height="14" viewBox="0 0 24 24"><path fill="#b2121e" d="M6.6 10.8a15 15 0 006.6 6.6l2.2-2.2a1 1 0 011-.25 11.4 11.4 0 003.6.57 1 1 0 011 1V20a1 1 0 01-1 1A17 17 0 013 4a1 1 0 011-1h3.5a1 1 0 011 1c0 1.25.2 2.45.57 3.6a1 1 0 01-.25 1z"/></svg>
  Call us Now : <strong>701-555-0148</strong>
</div>
<nav class="abs nav">
  <a class="active">Home</a><a>Welcome &amp; Information</a><a>Area Attractions</a><a>Welcome to Leeds</a><a>Rates</a><a>Who's Merle?</a><a>FAQ's</a><a>Where are we</a>
</nav>
<h1 class="abs hero-headline">HEART OF SOME OF THE GREATEST<br>HUNTING AND FISHING IN THE WORLD</h1>
<div class="abs dots"><span></span><span class="on"></span><span></span><span></span><span></span></div>

<!-- Welcome -->
<div class="abs welcome-text">
  <h2 class="title">Welcome to Merle's RV Park &amp;<br>Lodge and Leeds, North Dakota</h2>
  <p>Leeds is in the heart of some of the greatest hunting and fishing in the world. Merle's RV Park is located right on Highway 2 midway between Devils Lake and Rugby North Dakota. We are smack dab in the middle of it all!</p>
</div>
<div class="abs divider"></div>
<div class="abs portrait" role="img" aria-label="Portrait photo of Merle, the owner"></div>

<!-- Lodge + Meeting -->
<section class="abs band-grey" style="top:960px;height:1000px"></section>
<svg class="abs" style="left:0;top:900px" width="1200" height="110" viewBox="0 0 1200 110" preserveAspectRatio="none">
  <path d="M0 20 Q600 110 1200 60 L1200 110 L0 110 Z" fill="#f1f1f1"/>
  <path d="M0 20 Q600 110 1200 60 L1200 72 Q600 122 0 32 Z" fill="#b2121e"/>
</svg>
<div class="abs photo" style="left:130px;top:1065px;width:490px;height:245px;background:linear-gradient(135deg,#6b2e1c,#b86a3a 50%,#e2a55e)" role="img" aria-label="Photo of a cozy lodge bedroom with wood walls"></div>
<div class="abs copy" style="left:622px;top:1070px">
  <h2 class="title">Merle's Lodge</h2>
  <p>Are you looking for a cozy, but spacious home away from home? Well, you have found it! Merle's Lodge is 2200 square feet of living space. There are 2 spacious bedrooms with queen sized beds and another common sleeping area with 5 sets of bunk beds. Available to you are 2 restrooms with showers, a great room with dining and relaxing space and a full kitchen. Everything is supplied for you: towels, bedding, cookware, dishware, grill and etc...all that you need to make your stay worry and hassle free. Throw some clothes in a suitcase, hit the road and we will have your home away from home all ready when you get here! The Lodge is open all year round.</p>
</div>
<div class="abs photo" style="left:130px;top:1380px;width:490px;height:330px;background:linear-gradient(180deg,#7a1e26,#c9b7a8 45%,#e6e1da)" role="img" aria-label="Photo of the great room set with tables and chairs for a meeting"></div>
<div class="abs copy" style="left:622px;top:1380px">
  <h2 class="title">Meeting / Conference</h2>
  <p>Are you looking for a venue for your next meeting, training event, guys/girls weekend, quilt retreat, holiday gathering, family reunion, birthday, wedding party or get together? We've got you covered! Merle's Lodge seats about 45 people comfortably. Many of our customers have commented that Merle's was the perfect place for their event because it was so inviting...and just like home!</p>
  <ul class="bullets">
    <li>Groups – hunting, fishing, working, playing</li>
    <li>2200 square feet</li>
    <li>Full kitchen</li>
    <li>Free WiFi</li>
    <li>Satellite TV</li>
    <li>2 restrooms, one is handicap accessible</li>
    <li>Sleeps 14 – 2 bedrooms with queen sized beds, plus a shared sleeping area with bunk beds</li>
    <li>A great room with ample seating for large groups</li>
    <li>Merle supplies everything...bedding, towels, cookware, etc.</li>
    <li>Kids stay free.</li>
  </ul>
  <a class="btn-red" style="margin-top:22px">Read More</a>
</div>

<!-- RV Park -->
<div class="abs copy" style="left:130px;top:2050px;width:440px">
  <h2 class="title">Merle's RV PARK</h2>
  <p>Merle's RV Park sits right next to Highway 2 on the north side. We have 14 full service spaces – sewer, water and electric (20, 30, 50 amp). There is an indoor restroom with shower that is available 24 hours a day to our RV customers. Plenty of space is available to you for parking boats, trailers etc.</p>
  <p>Merle's RV Park year round, but water usage depends on when spring thaw and freeze up occurs.</p>
  <ul class="bullets">
    <li>14 Full Service Sites</li>
    <li>Electric (20, 30 &amp; 50amp), Water, Sewer</li>
    <li>Free WiFi</li>
    <li>Safe &amp; convenient location</li>
    <li>24 hour indoor restroom with shower</li>
    <li>Road Pass Club accepted for first night</li>
    <li>Ample room to park boats, trailers etc.</li>
    <li>Convenience store/gas station located right across the street. Restaurant onsite.</li>
    <li>Merle operates on a first come, first serve basis for short term stays. If you would like to reserve for a stay longer than 3 days, please call Merle.</li>
  </ul>
</div>
<div class="abs photo" style="left:640px;top:2025px;width:352px;height:540px;background:linear-gradient(180deg,#2c4f8e,#7fa0c8 40%,#3f5b3a 65%,#8a8f7c)" role="img" aria-label="Photo of an RV parked beneath tall trees"></div>

<!-- Tents -->
<section class="abs band-grey" style="top:2625px;height:410px"></section>
<div class="abs" style="left:150px;top:2660px;width:500px;height:330px;background:radial-gradient(ellipse at 50% 55%,#f5a623,#e8891a 45%,#f1f1f1 72%)" role="img" aria-label="Illustration of an orange camping tent"></div>
<div class="abs copy" style="left:700px;top:2670px;width:380px">
  <h2 class="title">Tents</h2>
  <p>There are many variations of passages of Lorem Ipsum available, but the majority have suffered alteration in some form, by injected humour, or randomised words which don't look even slightly believable. If you are going to use a passage.</p>
  <ul class="bullets">
    <li>Lorem Ipsum is simply dummy text</li>
    <li>There are many variations of passag</li>
    <li>Contrary to popular belief, Lorem</li>
    <li>It is a long established fact that</li>
    <li>Sed ut perspiciatis unde omnis</li>
  </ul>
</div>

<!-- Rates -->
<h2 class="abs title rates-title">Rates</h2>
<div class="abs card" style="left:130px">
  <h3>Merle's Lodge Pricing</h3>
  <div class="body">
    <div class="price">$200<small>for 24 hours</small></div>
    <hr>
    <p>The first 6 adults are included in the $200 per night rent.</p>
    <hr>
    <p>Each adult exceeding the initial 6, must pay $25 per night.</p>
    <hr>
    <p>Kids under age 16 stay free.</p>
  </div>
</div>
<div class="abs card" style="left:445px">
  <h3>Merle's RV Park Pricing</h3>
  <div class="body">
    <div class="label">RV SITES</div>
    <hr style="margin:8px 0">
    <div class="prices">
      <div class="price">$24<small>/ Night</small></div>
      <div class="price">$125<small>/ week</small></div>
      <div class="price">$375<small>/ month</small></div>
    </div>
    <p style="margin-top:12px">This price is for 4 adults. Any adults exceeding the initial 4, must pay $5 extra per night. Kids under 16 stay free.</p>
    <hr>
    <div class="label">TENT SITES <span class="price" style="font-size:22px">$12</span> / Night</div>
    <p style="margin-top:8px">This price is for 4 adults. Any adults exceeding the initial 4, must pay $3 extra per night. Kids under 16 stay free.</p>
  </div>
</div>
<div class="abs card" style="left:760px">
  <h3>Showers</h3>
  <div class="body">
    <p>Showers are $5 per person for unregistered customers.</p>
    <hr>
    <p>There is no charge for anyone that uses the shower that is staying at Merle's RV Park &amp; Lodge.</p>
  </div>
</div>

<!-- Reviews -->
<section class="abs reviews">
  <p>Find out what our customers are saying<br>about Merle's RV Park &amp; Lodge.</p>
  <a class="fb-btn"><span class="sq"><i></i></span><span class="t">CHECK OUT OUR FRIENDBOOK</span></a>
</section>

<!-- Footer -->
<footer class="abs footer">
  <div class="abs foot-brand"><span class="mark"></span>Merle's RV Park &amp; Lodge Leeds ND</div>
  <div class="abs follow">
    <h4>FOLLOW US</h4>
    <ul>
      <li><i></i>Friendbook</li>
      <li><i></i>Chirper</li>
      <li><i></i>WorkLink</li>
    </ul>
  </div>
  <div class="abs contact">
    <h4>CONTACT US</h4>
    <ul>
      <li><svg width="12" height="14" viewBox="0 0 24 28"><path fill="#ddd" d="M12 0a9 9 0 00-9 9c0 7 9 19 9 19s9-12 9-19a9 9 0 00-9-9zm0 12a3 3 0 110-6 3 3 0 010 6z"/></svg><span>120 Prairie Ave SE Leeds<br>ND 58346</span></li>
      <li><svg width="12" height="12" viewBox="0 0 24 24"><path fill="#ddd" d="M6.6 10.8a15 15 0 006.6 6.6l2.2-2.2a1 1 0 011-.25 11.4 11.4 0 003.6.57 1 1 0 011 1V20a1 1 0 01-1 1A17 17 0 013 4a1 1 0 011-1h3.5a1 1 0 011 1c0 1.25.2 2.45.57 3.6a1 1 0 01-.25 1z"/></svg><span>701-555-0148</span></li>
      <li><svg width="13" height="11" viewBox="0 0 26 20"><rect width="26" height="20" rx="2" fill="#ddd"/><path d="M1 2l12 9 12-9" stroke="#2d2d2d" stroke-width="2" fill="none"/></svg><span>merlesrvlodge@example.com</span></li>
    </ul>
  </div>
  <div class="abs map" role="img" aria-label="Map showing Leeds, North Dakota and the surrounding area"></div>
</footer>
<div class="abs copyright">Copyrights @ 2016 All Rights Reserved</div>

</body>
</html>
```